Electrician Letterhead Design MVR

We need some letterhead for our bills and other papers.
Customer address is on the right side (Swiss format)
A4 format

Design should also be applicable on Cards

Target Market(s)

Private Customers, Small Business

Industry/Entity Type

Electrician

Other font styles liked:
• incised 901

Colors
00AB8E
00BBA5
67D7C9
C6EFE9
E9F9F6

```html
<!DOCTYPE html>
<html lang="en">
<head>
<meta charset="utf-8">
<title>MVR Letterhead</title>
<link rel="stylesheet" href="https://fonts.googleapis.com/css2?family=Exo+2:wght@700&family=Ubuntu:wght@400;500&display=swap">
<style>
  :root {
    --teal-deep: #00AB8E;
    --teal: #00BBA5;
    --teal-soft: #67D7C9;
    --teal-pale: #C6EFE9;
    --teal-mist: #E9F9F6;
    --paper: #FFFFFF;
    --backdrop: #E6E6E6;
    --ink: #4A4A4A;
  }
  * { margin: 0; padding: 0; box-sizing: border-box; }
  html, body {
    width: 1200px; height: 800px; overflow: hidden;
    background: var(--backdrop);
  }
  .canvas {
    width: 1200px; height: 800px;
    display: flex; align-items: center; justify-content: center;
  }
  .letterhead {
    position: relative;
    width: 523px; height: 740px;
    background: var(--paper);
    overflow: hidden;
    box-shadow: 0 2px 10px rgba(0,0,0,0.08);
  }
  .brand {
    position: absolute; left: 40px; top: 62px;
    display: flex; flex-direction: column;
  }
  .brand-name {
    font-family: "Exo 2", sans-serif; font-weight: 700;
    font-size: 40px; line-height: 1; letter-spacing: 1px;
    color: var(--teal-deep);
    display: flex; align-items: center; gap: 8px;
  }
  .brand-mark {
    width: 12px; height: 12px; background: var(--teal-deep);
  }
  .brand-tagline {
    font-family: "Ubuntu", sans-serif; font-weight: 500;
    font-size: 8.5px; color: #333; margin-top: 3px; letter-spacing: 0.3px;
  }
  .contact {
    position: absolute; right: 34px; top: 34px; width: 150px;
    font-family: "Ubuntu", sans-serif; font-size: 7.5px; line-height: 1.45;
    color: var(--ink);
  }
  .contact-line { display: flex; align-items: center; gap: 4px; }
  .contact-icon {
    width: 7px; height: 7px; border-radius: 50%;
    background: var(--teal-deep); flex: none;
  }
  .faint-mark {
    position: absolute; left: 70px; bottom: 90px;
    width: 120px; height: 120px; background: var(--teal-mist);
  }
  .corner-swoosh {
    position: absolute; right: 0; bottom: 0; width: 523px; height: 740px;
  }
  .website {
    position: absolute; left: 40px; bottom: 34px;
    font-family: "Ubuntu", sans-serif; font-size: 10px; letter-spacing: 0.4px;
    color: var(--teal-deep);
  }
</style>
</head>
<body>
<main class="canvas">
  <article class="letterhead">
    <header class="brand">
      <div class="brand-name"><span>MVR</span><span class="brand-mark"></span></div>
      <div class="brand-tagline">Elektrotechnik Morvan GmbH</div>
    </header>

    <address class="contact">
      <div>Suite 102 Street name,</div>
      <div>State, Zip 2034, Country</div>
      <div class="contact-line"><span class="contact-icon"></span>+01-5550-123456</div>
      <div class="contact-line"><span class="contact-icon"></span>+01-5550-1234567</div>
      <div class="contact-line"><span class="contact-icon"></span>info@morvanelektro.com</div>
    </address>

    <div class="faint-mark"></div>

    <svg class="corner-swoosh" viewBox="0 0 523 740" aria-hidden="true">
      <path d="M150 740 Q470 715 523 520 L523 740 Z" fill="var(--teal-soft)"/>
      <path d="M200 740 Q480 722 523 560 L523 740 Z" fill="var(--teal)"/>
    </svg>

    <footer class="website">www.morvanelektro.com</footer>
  </article>
</main>
</body>
</html>
```